Coastal Learner Bureau business cards

Australian company about to start offering its services. We recruit international students to come to study English, vocational education and postgraduate courses in Australia. We help them find the institution and select the right city they want to come to Australia. We are a young, online oriented and supportive agency. Our clients are between 18 and 35 years old, mainly University students, young professionals or people with work experience. We provide much more information that any other agency offer. We administrate a Facebook group with more than 11.000 members that daily ask questions about general information when coming to Australia, while they are here and even after they leave the country

Target Market(s)

International students from South America, Central America and Europe

Industry/Entity Type

Student

Contact Information for Business Card

Tomas Bilbrea
Managing Director
tomas@kelvarin.com.au
www.kelvoria.com.au
+61 491058264
Melbourne, Australia

Font styles to use
Serif
Sans Serif

Colors

Designer to choose colors to be used in the design.

Requirements
Must have
• Horizontal design
• Standard business card size and shape. If font uses green or yellow colours, they will have to match the ones from the logo
Nice to have
• UPDATE: Use the contents of the green image to design one of the card sides. Use our logo in the background of that side as watermark.
• Passport image, or immigration stamps. A picture of the Yarra River (from Melbourne) would be cool as well.
Should not have
• Non-standard business card size and shape
• Not black as the background colour of any sides as we are not a VIP agency or a hight class service. We are orientes to young people and they like colours, pictures, something attractive.
• Vertical design
• NO YELLOW or BLACK AS THE BACKGROUND COLOUR OF ANY SIDE OF THE BIZ CARD

```html
<!DOCTYPE html>
<html lang="en">
<head>
<meta charset="utf-8">
<title>Coastal Learner Bureau business cards</title>
<link href="https://fonts.googleapis.com/css2?family=Roboto+Condensed:wght@700&family=Roboto:wght@400;500;700&display=swap" rel="stylesheet">
<style>
  :root {
    --brand-yellow: #e0b912;
    --brand-green: #135f3d;
    --brand-green-light: #2b7a55;
    --card-white: #f6f6f4;
    --page-bg: #e7e7e5;
    --text-light: #ffffff;
  }
  * { box-sizing: border-box; margin: 0; padding: 0; }
  html, body { width: 1200px; height: 886px; overflow: hidden; }
  body {
    background: var(--page-bg);
    font-family: "Roboto", sans-serif;
    position: relative;
  }
  .card {
    position: absolute;
    left: 320px;
    width: 560px;
    height: 320px;
    overflow: hidden;
    box-shadow: 0 6px 18px rgba(0,0,0,0.18);
  }
  .wordmark {
    font-family: "Roboto", sans-serif;
    font-weight: 700;
    letter-spacing: 0.5px;
    line-height: 1;
  }

  /* Front side */
  .card-front {
    top: 90px;
    background: linear-gradient(200deg, var(--brand-green) 55%, var(--brand-green-light) 100%);
    display: flex;
    align-items: center;
    justify-content: center;
  }
  .card-front .wordmark { color: var(--text-light); font-size: 54px; }

  /* Back side */
  .card-back { top: 476px; background: var(--card-white); }
  .back-logo-zone {
    position: absolute;
    left: 0; top: 0; bottom: 0;
    width: 220px;
    display: flex;
    align-items: center;
    justify-content: center;
  }
  .card-back .wordmark { color: var(--brand-green); font-size: 40px; }
  .back-info-zone {
    position: absolute;
    left: 220px; right: 0; top: 0; bottom: 0;
    background: linear-gradient(200deg, var(--brand-green) 55%, var(--brand-green-light) 100%);
  }
  .contact-block {
    position: absolute;
    left: 32px;
    top: 28px;
    color: var(--text-light);
  }
  .holder-name {
    font-family: "Roboto Condensed", sans-serif;
    font-weight: 700;
    font-size: 26px;
    color: var(--brand-yellow);
    text-transform: uppercase;
    line-height: 1;
  }
  .holder-role { font-size: 15px; margin-top: 4px; }
  .divider {
    width: 34px;
    height: 1px;
    background: var(--text-light);
    margin: 16px 0 14px 0;
  }
  .contact-line { font-size: 14px; line-height: 21px; white-space: nowrap; }
  .contact-line.location { margin-bottom: 8px; }
  .label { color: var(--brand-yellow); font-weight: 700; margin-right: 3px; }
  .tag-band { position: absolute; left: 0; bottom: 0; width: 340px; height: 70px; }
  .tagline {
    position: absolute;
    right: 20px;
    bottom: 16px;
    font-weight: 700;
    font-size: 14px;
    color: var(--text-light);
  }
</style>
</head>
<body>

  <section class="card card-front" aria-label="Card front">
    <span class="wordmark">Kelvoria</span>
  </section>

  <section class="card card-back" aria-label="Card back">
    <div class="back-logo-zone">
      <span class="wordmark">Kelvoria</span>
    </div>
    <div class="back-info-zone">
      <div class="contact-block">
        <p class="holder-name">Tomas Bilbrea</p>
        <p class="holder-role">Managing Director</p>
        <div class="divider"></div>
        <p class="contact-line location">Melbourne, Australia</p>
        <p class="contact-line"><span class="label">P:</span>+61 491058264</p>
        <p class="contact-line"><span class="label">E:</span>tomas@kelvarin.com.au</p>
        <p class="contact-line"><span class="label">W:</span>www.kelvoria.com.au</p>
      </div>
      <svg class="tag-band" viewBox="0 0 340 70" aria-hidden="true">
        <path d="M0 56 L140 56 C166 56 170 24 196 24 L340 24 L340 70 L0 70 Z" fill="var(--brand-yellow)"/>
      </svg>
      <p class="tagline">Hacemos más por ti!</p>
    </div>
  </section>

</body>
</html>
```